SkyvornQ Business Cards and Stationary Design

Need a design for our business cards and stationary. I want to carry on the theme of the logo. I want the business cards to have a design on the back. I would like the business cards and the stationary to carry the same theme, design scheme, and branding

Target Market(s)

Airlines and Maintenance Facilities

Industry/Entity Type

Aviation

Contact Information for Business Card

Name
Position Title
Address: 4827 Trellis Hollow Road, Fort Pierce, Florida, 34951
Office Number
Mobile Number
Email
Website

Font styles to use
Serif
Sans Serif

Colors

Designer to choose colors to be used in the design.

```html
<!DOCTYPE html>
<html lang="en">
<head>
<meta charset="utf-8">
<title>SkyvornQ Business Card</title>
<link href="https://fonts.googleapis.com/css2?family=Montserrat:wght@600;700&family=Source+Sans+3:wght@400;600&display=swap" rel="stylesheet">
<style>
  :root {
    --backdrop: #e6e8ec;
    --card: #ffffff;
    --navy: #0d2a5c;
    --blue: #0b84d2;
    --blue-mid: #0d5fae;
    --ink: #2a2f38;
    --grey: #555b66;
    --white: #ffffff;
  }
  * { box-sizing: border-box; margin: 0; padding: 0; }
  html, body { width: 1200px; height: 872px; overflow: hidden; }
  body {
    background: var(--backdrop);
    font-family: "Source Sans 3", Arial, sans-serif;
    display: flex;
    align-items: center;
    justify-content: center;
    gap: 40px;
  }
  .card {
    position: relative;
    width: 540px;
    height: 309px;
    background: var(--card);
    box-shadow: 0 6px 22px rgba(20, 30, 50, 0.18);
    overflow: hidden;
  }

  /* Back side */
  .card-back { display: flex; flex-direction: column; align-items: center; justify-content: center; }
  .brand { display: flex; align-items: center; gap: 16px; }
  .brand-mark {
    width: 56px; height: 56px; border-radius: 50%;
    border: 6px solid var(--blue-mid);
  }
  .brand-name {
    font-family: "Montserrat", Arial, sans-serif;
    font-weight: 700;
    color: var(--navy);
    letter-spacing: 5px;
    font-size: 38px;
  }
  .card-back .website {
    margin-top: 18px;
    font-size: 15px;
    letter-spacing: 4px;
    color: var(--ink);
  }

  /* Front side */
  .holder { position: absolute; top: 22px; right: 26px; text-align: right; }
  .holder-name {
    font-family: "Montserrat", Arial, sans-serif;
    font-weight: 700; font-size: 19px; color: var(--navy); letter-spacing: 0.3px;
  }
  .holder-title { font-size: 17px; color: var(--grey); letter-spacing: 0.5px; }
  .card-front .brand { position: absolute; left: 40px; top: 92px; }
  .card-front .brand-name { font-size: 34px; }
  .address {
    position: absolute; left: 40px; top: 200px;
    font-size: 13.5px; color: var(--ink); line-height: 1.4;
    display: flex; gap: 6px;
  }
  .address svg { flex: none; margin-top: 2px; }
  .band { position: absolute; inset: 0; }
  .contacts {
    position: absolute; right: 24px; bottom: 22px;
    list-style: none; text-align: right;
    color: var(--white); font-size: 13.5px; line-height: 1.55;
  }
  .contacts li { display: flex; align-items: center; justify-content: flex-end; gap: 6px; }
</style>
</head>
<body>

  <section class="card card-back" aria-label="Business card back">
    <div class="brand">
      <span class="brand-mark"></span>
      <span class="brand-name">SKYVORNQ</span>
    </div>
    <p class="website">www.skyvornq.com</p>
  </section>

  <section class="card card-front" aria-label="Business card front">
    <svg class="band" viewBox="0 0 540 309" width="540" height="309" role="img" aria-label="Decorative blue band along the lower edge">
      <defs>
        <linearGradient id="bandFill" x1="0" y1="1" x2="1" y2="0">
          <stop offset="0" stop-color="#0b84d2"/>
          <stop offset="1" stop-color="#0d2f74"/>
        </linearGradient>
      </defs>
      <path d="M0,300 Q330,300 540,140 L540,309 L0,309 Z" fill="url(#bandFill)"/>
    </svg>

    <div class="holder">
      <p class="holder-name">MARCUS DELANEY</p>
      <p class="holder-title">PRESIDENT</p>
    </div>

    <div class="brand">
      <span class="brand-mark"></span>
      <span class="brand-name">SKYVORNQ</span>
    </div>

    <div class="address">
      <svg width="11" height="14" viewBox="0 0 11 14" aria-hidden="true">
        <path d="M5.5 0.8a4.4 4.4 0 0 1 4.4 4.4c0 3.2-4.4 8-4.4 8s-4.4-4.8-4.4-8A4.4 4.4 0 0 1 5.5 0.8z" fill="none" stroke="#0d5fae" stroke-width="1.4"/>
        <circle cx="5.5" cy="5.2" r="1.6" fill="#0d5fae"/>
      </svg>
      <p>123, Street Name, City Name<br>Zipcode-012345</p>
    </div>

    <ul class="contacts">
      <li>
        <svg width="12" height="12" viewBox="0 0 12 12" aria-hidden="true"><circle cx="6" cy="6" r="5.3" fill="none" stroke="#fff" stroke-width="1"/><path d="M4 3.5l1 1.3-.6.8c.4.8 1 1.4 1.8 1.8l.8-.6 1.3 1-.6 1C5.8 8.6 3.4 6.2 3.2 4.1z" fill="#fff"/></svg>
        772-555-0148
      </li>
      <li>
        <svg width="12" height="12" viewBox="0 0 12 12" aria-hidden="true"><circle cx="6" cy="6" r="5.3" fill="none" stroke="#fff" stroke-width="1"/><rect x="4.3" y="3" width="3.4" height="6" rx="0.6" fill="none" stroke="#fff" stroke-width="1"/></svg>
        772-555-0193
      </li>
      <li>
        <svg width="12" height="12" viewBox="0 0 12 12" aria-hidden="true"><circle cx="6" cy="6" r="5.3" fill="none" stroke="#fff" stroke-width="1"/><rect x="3.2" y="4" width="5.6" height="4" fill="none" stroke="#fff" stroke-width="0.9"/><path d="M3.2 4l2.8 2.2L8.8 4" fill="none" stroke="#fff" stroke-width="0.9"/></svg>
        info@skyvornq.com
      </li>
      <li>
        <svg width="12" height="12" viewBox="0 0 12 12" aria-hidden="true"><circle cx="6" cy="6" r="5.3" fill="none" stroke="#fff" stroke-width="1"/><ellipse cx="6" cy="6" rx="2.2" ry="5.3" fill="none" stroke="#fff" stroke-width="0.8"/><path d="M0.8 6h10.4" stroke="#fff" stroke-width="0.8"/></svg>
        www.skyvornq.com
      </li>
    </ul>
  </section>

</body>
</html>
```